BOLD & MINIMALIST DESIGN NEEDED

We want a very bold but minimalistic business card design that is impactful and utilizes both sides of the business card. Our current logo is included for your use.

We want bold fonts and good use of negative space. We don't want the logo to overpower the design.

Target Market(s)

Professionals who are building new commercial buildings.

Industry/Entity Type

Construction

Contact Information for Business Card

Name, Title, email, office phone, cell phone, website

Font styles to use
Serif
Sans Serif

Requirements
Must have
• Bold design!

```html
<!DOCTYPE html>
<html lang="en">
<head>
<meta charset="utf-8">
<title>Stonegate Design + Build – Business Card</title>
<link rel="stylesheet" href="https://fonts.googleapis.com/css2?family=Montserrat:wght@400;500;800;900&display=swap">
<style>
  :root {
    --bg: #2e2e2e;
    --green: #86c440;
    --ink: #111111;
    --white: #ffffff;
    --grey-text: #222222;
  }
  * { margin: 0; padding: 0; box-sizing: border-box; }
  html, body { width: 1200px; height: 689px; overflow: hidden; background: var(--bg); }
  body { font-family: "Montserrat", Arial, sans-serif; position: relative; }

  .card {
    position: absolute;
    top: 190px;
    width: 540px;
    height: 310px;
    border-radius: 22px;
    overflow: hidden;
  }
  .card--front { left: 40px; background: var(--green); }
  .card--back { left: 620px; background: var(--white); }

  /* Front */
  .front-brand {
    position: absolute; inset: 0;
    display: flex; align-items: center; justify-content: center; gap: 16px;
    color: var(--white);
  }
  .brand-mark { width: 34px; height: 34px; background: var(--white); flex: none; }
  .brand-name {
    font-weight: 900; font-size: 44px; letter-spacing: 1px; line-height: 0.95;
    text-transform: uppercase;
  }

  /* Back */
  .back-shape { position: absolute; inset: 0; width: 540px; height: 310px; }
  .holder {
    position: absolute; top: 28px; right: 36px; text-align: right;
  }
  .holder-name { color: var(--green); font-weight: 800; font-size: 26px; letter-spacing: 0.5px; }
  .holder-title { color: var(--grey-text); font-weight: 500; font-size: 12px; letter-spacing: 1px; margin-top: 2px; }
  .holder-bar {
    position: absolute; top: 26px; right: 0; width: 20px; height: 36px; background: var(--green);
  }
  .back-brand {
    position: absolute; left: 32px; top: 98px;
    display: flex; align-items: center; gap: 10px; color: var(--ink);
  }
  .back-brand .brand-mark { width: 22px; height: 22px; background: var(--ink); }
  .back-brand .brand-name { font-size: 26px; }

  .contact {
    position: absolute; left: 30px; bottom: 16px; list-style: none;
    color: var(--white); font-size: 12.5px; font-weight: 500;
  }
  .contact li { display: flex; align-items: center; gap: 8px; line-height: 19px; }
  .contact svg { width: 12px; height: 12px; fill: var(--white); flex: none; }

  .address {
    position: absolute; right: 32px; bottom: 22px; text-align: right;
    color: var(--white); font-size: 13px; font-weight: 500; font-style: normal; line-height: 19px;
  }
</style>
</head>
<body>

  <section class="card card--front" aria-label="Card front">
    <div class="front-brand">
      <span class="brand-mark"></span>
      <span class="brand-name">Stonegate<br>Design + Build</span>
    </div>
  </section>

  <section class="card card--back" aria-label="Card back">
    <svg class="back-shape" viewBox="0 0 540 310" aria-hidden="true">
      <path d="M0,190 Q300,182 540,118 L540,132 Q300,198 0,204 Z" fill="var(--ink)"/>
      <path d="M0,204 Q300,198 540,132 L540,310 L0,310 Z" fill="var(--green)"/>
    </svg>

    <div class="holder">
      <div class="holder-name">MARCUS REED</div>
      <div class="holder-title">OWNER-CEO</div>
    </div>
    <div class="holder-bar"></div>

    <div class="back-brand">
      <span class="brand-mark"></span>
      <span class="brand-name">Stonegate<br>Design + Build</span>
    </div>

    <ul class="contact">
      <li><svg viewBox="0 0 24 24"><path d="M6.6 10.8a15 15 0 0 0 6.6 6.6l2.2-2.2a1 1 0 0 1 1-.25 11.4 11.4 0 0 0 3.6.57 1 1 0 0 1 1 1V20a1 1 0 0 1-1 1A17 17 0 0 1 3 4a1 1 0 0 1 1-1h3.5a1 1 0 0 1 1 1c0 1.25.2 2.45.57 3.57a1 1 0 0 1-.25 1z"/></svg>555 204 7781</li>
      <li><svg viewBox="0 0 24 24"><path d="M7 1h10a2 2 0 0 1 2 2v18a2 2 0 0 1-2 2H7a2 2 0 0 1-2-2V3a2 2 0 0 1 2-2zm0 3v15h10V4zm5 16.2a1 1 0 1 0 0 .1z"/></svg>555 318 6620</li>
      <li><svg viewBox="0 0 24 24"><path d="M2 5h20v14H2zm2 2v.5l8 5 8-5V7zm0 2.8V17h16V9.8l-8 5z"/></svg>hello@stonegatebuild.com</li>
      <li><svg viewBox="0 0 24 24"><path d="M12 2a10 10 0 1 0 0 20 10 10 0 0 0 0-20zm0 2a8 8 0 0 1 7.7 6H16a13 13 0 0 0-2-5.7A8 8 0 0 1 12 4zm-2 .3A13 13 0 0 0 8 10H4.3A8 8 0 0 1 10 4.3zM4.3 14H8a13 13 0 0 0 2 5.7A8 8 0 0 1 4.3 14zm9.7 5.7A13 13 0 0 0 16 14h3.7a8 8 0 0 1-5.7 5.7z"/></svg>www.stonegatebuild.com</li>
    </ul>

    <address class="address">48 Quarry Lane, Fairmont<br>OH 45011</address>
  </section>

</body>
</html>
```